Velvet Moon Wheel Method Needs a Website

I require a PressKit website so that I can do simple edits myself. I want it to be a fairly simple design as the videos and the text will speak for themselves.
The concept is simple, we have developed a revolutionary roulette system that proves the game is NOT random. This breakthrough is absolutely massive. We are offering a 12-part training course to take a beginner to a professional at their own pace through watching videos made by our roulette genius.
Roulette and casinos have a glitzy feel about them and this should be reflected in the style of the site. The roulette wheel, table and chips are very evocative and pictures of these would be good.
There is a home page and 5 other pages containing sub-pages. These should be interlinked and it must be easy to get back to the home page from anywhere on the site.
Coinvey links should appear at the bottom of each page.
I really need the site in a hurry as we were let down badly by the last developer we hired who went on holiday and left us in the lurch.

Target Market(s)

Gamblers, betting community, opportunity seekers

Coding

Coded - Design and coding required

Number of Pages Required

1 page

Font styles to use
Sans Serif

Requirements
Must have
• At least two videos on the Home page.
• Coinvey details on every page and tab.
• A box for name and email address for interested parties to leave their details.

```html
<!DOCTYPE html>
<html lang="en">
<head>
<meta charset="utf-8">
<title>Welcome to My Blog – Velvet Moon Wheel Method</title>
<link rel="stylesheet" href="https://fonts.googleapis.com/css2?family=Montserrat:wght@400;600&display=swap">
<style>
:root{
  --brand-blue:#2ea3f2;
  --ink:#333333;
  --muted:#666666;
  --rule:#e2e2e2;
  --field:#eeeeee;
  --footer:#222222;
  --footer-text:#666666;
  --white:#ffffff;
}
*{margin:0;padding:0;box-sizing:border-box}
html,body{width:800px;height:1200px;overflow:hidden;background:var(--white)}
body{position:relative;font-family:"Montserrat",sans-serif;color:var(--muted)}

.site-header{position:absolute;top:0;left:0;width:800px;height:26px;background:var(--white);box-shadow:0 1px 0 rgba(0,0,0,.05)}
.brand{position:absolute;left:83px;top:6px;display:flex;align-items:center;gap:4px;font-size:11px;color:#555;font-weight:400;letter-spacing:.5px}
.brand-dot{width:13px;height:13px;border:1px solid #555;border-radius:50%}
.main-nav{position:absolute;right:100px;top:9px;display:flex;gap:17px;font-size:6.3px;font-weight:600;color:#555;letter-spacing:.3px}
.main-nav .current{color:var(--brand-blue)}
.nav-search{position:absolute;right:80px;top:9px}

.page-banner{position:absolute;top:26px;left:0;width:800px;height:59px;background:var(--brand-blue);color:var(--white)}
.page-banner h1{position:absolute;left:80px;top:17px;font-size:12.5px;font-weight:600;letter-spacing:1px}
.page-banner p{position:absolute;left:80px;top:33px;font-size:6px;font-weight:600;letter-spacing:.3px}

.post{position:absolute;left:80px;width:415px}
.post-thumb{display:block;width:415px}
.post-title{margin-top:9px;font-size:10.8px;line-height:8.5px;font-weight:600;color:var(--ink);letter-spacing:1.1px}
.post-meta{margin-top:3px;font-size:6px;color:var(--muted);letter-spacing:.3px}
.post-excerpt{margin-top:2px;font-size:6.2px;line-height:7.5px;color:var(--muted);letter-spacing:.38px}

.sidebar{position:absolute;left:530px;top:110px;width:190px;height:112px;border-right:1px solid var(--rule);padding-right:20px}
.sidebar h4{font-size:8px;font-weight:600;color:var(--ink);letter-spacing:.6px;margin-bottom:1px}
.sidebar li{list-style:none;font-size:6.2px;line-height:7.3px;color:var(--muted);margin-bottom:2.3px;letter-spacing:.5px}

.signup{position:absolute;left:530px;top:240px;width:170px}
.signup h4{font-size:8px;font-weight:600;color:var(--ink);letter-spacing:.6px;margin-bottom:5px}
.signup .field{height:16px;background:var(--field);margin-bottom:4px;font-size:6px;color:#999;padding:5px 6px;letter-spacing:.3px}
.signup .button{display:inline-block;height:15px;padding:4px 10px;border:1px solid var(--brand-blue);color:var(--brand-blue);font-size:6px;font-weight:600;letter-spacing:.4px}

.site-footer{position:absolute;left:0;top:1182px;width:800px;height:18px;background:var(--footer)}
.site-footer p{position:absolute;left:80px;top:5px;font-size:5.5px;color:var(--footer-text);letter-spacing:.3px}
.social{position:absolute;right:88px;top:4px;display:flex;gap:17px}
.social span{width:9px;height:9px;border-radius:50%;background:var(--footer-text)}
</style>
</head>
<body>

<header class="site-header">
  <div class="brand"><span class="brand-dot"></span>Orbita</div>
  <nav class="main-nav">
    <span>Home</span><span>About</span><span>Services &#8964;</span><span>Contact</span><span>Login</span><span class="current">Blog</span>
  </nav>
  <svg class="nav-search" width="9" height="9" viewBox="0 0 9 9"><circle cx="5" cy="4" r="2.8" fill="none" stroke="#777" stroke-width="1"/><line x1="3" y1="6" x2="1" y2="8" stroke="#777" stroke-width="1"/></svg>
</header>

<section class="page-banner">
  <h1>Welcome to My Blog</h1>
  <p>Stay up to date with our most recent news and updates</p>
</section>

<article class="post" style="top:110px">
  <svg class="post-thumb" height="128" role="img" aria-label="Video: online roulette betting table with numbered grid, chips and wheel previews"><defs><linearGradient id="g1" x1="0" y1="0" x2="0" y2="1"><stop offset="0" stop-color="#7a1a1e"/><stop offset=".7" stop-color="#5a0f12"/><stop offset="1" stop-color="#1e1e1e"/></linearGradient></defs><rect width="415" height="128" fill="url(#g1)"/><circle cx="207" cy="64" r="15" fill="rgba(0,0,0,.45)"/><path d="M202 56 L215 64 L202 72 Z" fill="#fff"/></svg>
  <h2 class="post-title">The Best Roulette Strategy Ever – Explained!</h2>
  <div class="post-meta">by admin</div>
  <p class="post-excerpt">If you (finally) got tired of blaming your bad luck for your poor results at the roulette table, you are left with two choices. You can quit the game and do not play roulette ever again in your life, or you can read this article and learn how to use my proven strategy to win money at online roulette. It's your call. One thing you should know</p>
</article>

<article class="post" style="top:319px">
  <svg class="post-thumb" height="139" role="img" aria-label="Video: live casino roulette tables with a green betting layout"><defs><linearGradient id="g2" x1="0" y1="0" x2="0" y2="1"><stop offset="0" stop-color="#5a2418"/><stop offset=".45" stop-color="#1f7a3a"/><stop offset="1" stop-color="#222"/></linearGradient></defs><rect width="415" height="139" fill="url(#g2)"/><circle cx="207" cy="69" r="15" fill="rgba(0,0,0,.45)"/><path d="M202 61 L215 69 L202 77 Z" fill="#fff"/></svg>
  <h2 class="post-title">Live Online Roulette Casino Reviews</h2>
  <div class="post-meta">by admin</div>
  <p class="post-excerpt">This casino streams live video from a real casino. If you only trust spins from a real land-based casino that anyone can physically walk in and play, this one's for you. The only downside is sometimes the tables get busy and the wheel spins infrequently, although there are other wheels provided that spin more frequently.</p>
</article>

<article class="post" style="top:539px">
  <svg class="post-thumb" height="111" role="img" aria-label="Close-up of a roulette wheel with a white ball on the numbered pockets"><defs><linearGradient id="g3" x1="0" y1="0" x2="1" y2="1"><stop offset="0" stop-color="#b3201e"/><stop offset=".5" stop-color="#1a1a1a"/><stop offset="1" stop-color="#4a4a4a"/></linearGradient></defs><rect width="415" height="111" fill="url(#g3)"/></svg>
  <h2 class="post-title">The Best and Worst Roulette Strategies Revealed</h2>
  <div class="post-meta">by admin</div>
  <p class="post-excerpt">A roulette strategy is basically any method to win at roulette. In most cases it's a set of mechanical rules that tell the player when and where to bet. There are more strategies to win roulette than any other casino game, but the vast majority of roulette players consistently lose. This page gives a simple explanation of which roulette strategies work.</p>
</article>

<article class="post" style="top:730px">
  <svg class="post-thumb" height="121" role="img" aria-label="Small electronic devices resting on a wooden roulette wheel"><defs><linearGradient id="g4" x1="0" y1="0" x2="0" y2="1"><stop offset="0" stop-color="#c9b8a8"/><stop offset=".5" stop-color="#6e3a22"/><stop offset="1" stop-color="#2a1a14"/></linearGradient></defs><rect width="415" height="121" fill="url(#g4)"/></svg>
  <h2 class="post-title">Roulette Computers: Hidden Devices That Predict The Winning Number</h2>
  <div class="post-meta">by admin</div>
  <p class="post-excerpt">Roulette computers are hidden electronic devices that predict where the ball will land. They calculate the speed and deceleration of ball and wheel to determine the approximate winning wheel sector. They are by far the quickest and most effective way to beat roulette. Many roulette computers exist, but most are simplistic and only win</p>
</article>

<article class="post" style="top:941px">
  <svg class="post-thumb" height="128" role="img" aria-label="Illustrated golden roulette wheel with gold coins, playing cards and casino chips"><defs><linearGradient id="g5" x1="0" y1="0" x2="1" y2="0"><stop offset="0" stop-color="#6a2a6e"/><stop offset=".35" stop-color="#b8862a"/><stop offset=".7" stop-color="#8a7aa8"/><stop offset="1" stop-color="#e8e4ee"/></linearGradient></defs><rect width="415" height="128" fill="url(#g5)"/></svg>
  <h2 class="post-title">The Roulette Systems &amp; Strategies That Are Winning Fortunes, and How To Get Them Free</h2>
  <div class="post-meta">by admin</div>
  <p class="post-excerpt">Roulette is not the unbeatable game that most people think. But there are only a few roulette systems that actually work. If you are tired of the rubbish written by people with no real experience and want the real facts about winning roulette strategies, this is the site you're looking for. You could spend days reading everything</p>
</article>

<aside class="sidebar">
  <h4>Search our blog....</h4>
  <ul>
    <li>The Best Roulette Strategy Ever – Explained!</li>
    <li>Live Online Roulette Casino Reviews</li>
    <li>The Best and Worst Roulette Strategies Revealed</li>
    <li>Roulette Computers: Hidden Devices That Predict The Winning Number</li>
    <li>The Roulette Systems &amp; Strategies That Are Winning Fortunes, and How To Get Them Free</li>
  </ul>
</aside>

<form class="signup">
  <h4>Join the Velvet Moon list</h4>
  <div class="field">Name</div>
  <div class="field">Email address</div>
  <span class="button">Send my details</span>
</form>

<footer class="site-footer">
  <p>Designed by Lumen Studio | Powered by PressKit | Secure payments with Coinvey</p>
  <div class="social"><span></span><span></span><span></span><span></span></div>
</footer>

</body>
</html>
```